Fresh, modern, fun business card for pediatric dental practice

Need a business card for fresh, modern, fun pediatric dental practice

Clean look that matches our website's font and colors

We prefer the look of curved corners on business cards

Target Market(s)

parents (mothers) of young children, professionals, mid-high class

Industry/Entity Type

Dental

Contact Information for Business Card

Maplebrook Pediatric Dentistry
482 Quarry Lane
Suite 517
Fernhollow, PA 17988
717.555.0193
www.maplebrooksmiles.example

Mei-Ran Tsai, DMD
Corinne Walbeck, DMD
(we are working on our email address, but we would like that on the card as well)

Font styles to use
Sans Serif

Requirements
Must have
• All info; we would also like to make cards for individual staff members
• colors from our website and color palatte, attatched
• use same font and design as website for branding
Nice to have
• clean, simple card that has a pop of color
• we would like to see a few designs with our tag line "where smiles get brighter"
• we are not sure if we want to have it on there or not
• we would like to see a few designs incorporating the ribbon graphic on our website where the word WELCOME is

```html
<!DOCTYPE html>
<html lang="en">
<head>
<meta charset="utf-8">
<title>Maplebrook Pediatric Dentistry – Business Card</title>
<link rel="stylesheet" href="https://fonts.googleapis.com/css2?family=Montserrat:wght@700&family=Work+Sans:wght@400;600&display=swap">
<style>
  :root {
    --backdrop: #3b3431;
    --card: #1c1c1c;
    --card-edge: #262626;
    --sun-yellow: #f7b21b;
    --text-light: #e4e4e4;
    --text-muted: #bdbdbd;
  }
  * { box-sizing: border-box; margin: 0; padding: 0; }
  html, body {
    width: 1200px; height: 715px; overflow: hidden;
    background: var(--backdrop);
  }
  .stage {
    width: 1200px; height: 715px;
    display: flex; align-items: center; justify-content: center; gap: 60px;
  }
  .card {
    position: relative;
    width: 520px; height: 297px;
    border-radius: 14px;
    background: var(--card);
    box-shadow: 0 0 0 1px var(--card-edge), 0 12px 30px rgba(0,0,0,.35);
    overflow: hidden;
  }
  .brand {
    font-family: "Work Sans", sans-serif;
    font-weight: 600;
    color: var(--sun-yellow);
    line-height: 1.05;
    display: flex; align-items: center; gap: 12px;
  }
  .brand-dot {
    width: 18px; height: 18px; border-radius: 50%;
    background: var(--sun-yellow); flex: none;
  }
  .brand-name .word { display: block; }
  /* front */
  .card-front { display: flex; align-items: center; justify-content: center; }
  .card-front .brand-name .word:first-child { font-size: 44px; letter-spacing: 1px; }
  .card-front .brand-name .word:last-child { font-size: 21px; letter-spacing: 1.5px; }
  /* back */
  .accent-bar {
    position: absolute; left: 0; top: 52px;
    width: 12px; height: 190px;
    background: var(--sun-yellow);
    border-radius: 0 12px 12px 0;
  }
  .contact {
    position: absolute; left: 42px; top: 60px; width: 240px;
    font-family: "Work Sans", sans-serif;
    color: var(--text-light);
  }
  .person-name {
    font-family: "Montserrat", sans-serif;
    font-weight: 700; font-size: 20px; letter-spacing: .5px;
    color: var(--sun-yellow); text-transform: uppercase;
    white-space: nowrap;
  }
  .person-title { font-size: 11px; color: var(--text-muted); margin-top: 2px; }
  .address { font-size: 12.5px; line-height: 1.4; margin-top: 16px; }
  .contact-list { list-style: none; margin-top: 8px; font-size: 12.5px; line-height: 1.55; }
  .contact-list li { display: flex; align-items: center; gap: 8px; white-space: nowrap; }
  .contact-list svg { width: 10px; height: 10px; flex: none; }
  .card-back .brand { position: absolute; right: 32px; top: 110px; }
  .card-back .brand-dot { width: 14px; height: 14px; }
  .card-back .brand-name .word:first-child { font-size: 32px; letter-spacing: .5px; }
  .card-back .brand-name .word:last-child { font-size: 15px; letter-spacing: 1px; }
</style>
</head>
<body>
<main class="stage">
  <section class="card card-front" aria-label="Card front">
    <div class="brand">
      <span class="brand-dot"></span>
      <span class="brand-name"><span class="word">maplebrook</span><span class="word">pediatric dentistry</span></span>
    </div>
  </section>

  <section class="card card-back" aria-label="Card back">
    <div class="accent-bar"></div>
    <div class="contact">
      <p class="person-name">Corinne Walbeck</p>
      <p class="person-title">DMD</p>
      <p class="address">482 Quarry Lane<br>Suite 517 Fernhollow, PA 17988</p>
      <ul class="contact-list">
        <li>
          <svg viewBox="0 0 10 10" aria-hidden="true"><path d="M2 1l2 2-1 1.2c.6 1.2 1.5 2.1 2.8 2.8L7 6l2 2-1.2 1.2C4.5 9 1 5.5.8 2.2z" fill="var(--sun-yellow)"/></svg>
          717.555.0193
        </li>
        <li>
          <svg viewBox="0 0 10 10" aria-hidden="true"><rect x=".8" y="2" width="8.4" height="6" rx=".8" fill="none" stroke="var(--sun-yellow)" stroke-width="1"/><path d="M1 2.5l4 3 4-3" fill="none" stroke="var(--sun-yellow)" stroke-width="1"/></svg>
          hello@maplebrooksmiles.example
        </li>
        <li>
          <svg viewBox="0 0 10 10" aria-hidden="true"><circle cx="5" cy="5" r="4.2" fill="none" stroke="var(--sun-yellow)" stroke-width="1"/><ellipse cx="5" cy="5" rx="1.8" ry="4.2" fill="none" stroke="var(--sun-yellow)" stroke-width=".8"/><path d="M.8 5h8.4" stroke="var(--sun-yellow)" stroke-width=".8"/></svg>
          www.maplebrooksmiles.example
        </li>
      </ul>
    </div>
    <div class="brand">
      <span class="brand-dot"></span>
      <span class="brand-name"><span class="word">maplebrook</span><span class="word">pediatric dentistry</span></span>
    </div>
  </section>
</main>
</body>
</html>
```